Orbit Voltix VR is the name of our project, We are a Virtual Reality Theme park

We need a web page and logo that is sharp and exciting, and futuristic that people would want to have on a tee shirt.. We like teal -black- silver colour. Customers will be able to book on line- we will have Free Roam VR experiences , Trundla(treadmills), Stand alone VR stations and VR Simulator rides.

Orbit Voltix VR

```html
<!DOCTYPE html>
<html lang="en">
<head>
<meta charset="utf-8">
<title>Orbit Voltix VR – Virtual Reality Theme Park</title>
<link href="https://fonts.googleapis.com/css2?family=Exo+2:wght@600;700;800&family=Open+Sans:ital,wght@0,400;0,600;1,400&family=Arimo:wght@400;700&display=swap" rel="stylesheet">
<style>
  :root {
    --teal: #1f9e9b;
    --teal-dark: #136e6c;
    --teal-light: #7fc9c6;
    --ink: #1b1b1b;
    --graphite: #2a2a2a;
    --silver: #c9cccd;
    --muted: #6d6d6d;
    --white: #ffffff;
    --star: #f7d117;
  }
  * { box-sizing: border-box; margin: 0; padding: 0; }
  html, body { width: 1200px; height: 3279px; overflow: hidden; background: var(--white); }
  .page { position: relative; width: 1200px; height: 3279px; overflow: hidden; font-family: "Open Sans", sans-serif; color: var(--ink); }
  .abs { position: absolute; }
  .heading { font-family: "Exo 2", sans-serif; font-weight: 700; text-transform: uppercase; }
  .btn { position: absolute; display: flex; align-items: center; justify-content: center; border-radius: 30px; font-family: "Arimo", sans-serif; font-weight: 700; font-size: 17px; text-transform: uppercase; }

  /* Hero */
  .hero-photo { left: 0; top: 0; width: 1200px; height: 780px;
    background: linear-gradient(120deg, #3a4a4a 0%, #5c5043 30%, #8a6b35 55%, #b89a3c 72%, #6c5a3e 100%); }
  .hero-shade { left: 0; top: 0; width: 1200px; height: 780px; background: linear-gradient(180deg, rgba(0,0,0,.45) 0%, rgba(0,0,0,.15) 40%, rgba(0,0,0,.25) 100%); }
  .site-header { left: 0; top: 0; width: 1200px; height: 110px; }
  .brand { left: 157px; top: 36px; font-family: "Arimo", sans-serif; font-weight: 700; font-size: 30px; color: var(--white); }
  .main-nav { left: 500px; top: 44px; display: flex; gap: 36px; font-family: "Arimo", sans-serif; font-weight: 700; font-size: 17px; color: var(--white); }
  .hero-title { left: 0; top: 258px; width: 1200px; text-align: center; color: var(--white); font-size: 54px; line-height: 1; letter-spacing: 1px; }
  .hero-sub { left: 0; top: 320px; width: 1200px; text-align: center; color: var(--white); font-size: 36px; line-height: 1; }
  .btn-hero { left: 500px; top: 372px; width: 194px; height: 57px; background: var(--teal); color: var(--white); }
  .slider-dots { left: 555px; top: 580px; display: flex; gap: 12px; }
  .slider-dots span { width: 18px; height: 18px; border-radius: 50%; border: 2px solid var(--white); }
  .slider-dots span.active { background: var(--white); }

  /* About */
  .about-photo { left: 165px; top: 751px; width: 400px; height: 400px; border-radius: 50%;
    background: linear-gradient(160deg, #d5e4f0 0%, #7fa8cf 45%, #3b6fae 70%, #8a5a3a 100%); }
  .about-title { left: 608px; top: 792px; font-size: 36px; line-height: 1.05; color: var(--ink); }
  .about-title span { color: var(--teal); display: block; }
  .about-text { left: 608px; top: 878px; width: 440px; font-size: 15.5px; line-height: 26px; color: var(--muted); }
  .btn-outline { border: 2px solid var(--teal); color: var(--teal); background: transparent; }
  .btn-about { left: 614px; top: 1038px; width: 174px; height: 55px; }

  /* Services & testimonials backdrop */
  .dark-photo { left: 0; top: 1400px; width: 1200px; height: 900px;
    background: linear-gradient(180deg, #1c1c1c 0%, #2b2b2b 40%, #3a3a3a 70%, #252525 100%); }
  .services-shape { left: 0; top: 1150px; }
  .services-title { left: 0; top: 1244px; width: 1200px; text-align: center; color: var(--white); font-size: 31px; }
  .service-card { position: absolute; width: 204px; height: 262px; border: 3px solid #8d8f90; border-radius: 4px; overflow: hidden; }
  .service-card .photo { position: absolute; inset: 0; }
  .service-card .label { position: absolute; left: 0; width: 100%; text-align: center; color: var(--white); font-family: "Arimo", sans-serif; font-weight: 700; font-size: 18px; line-height: 24px; text-transform: uppercase; }
  .service-card svg { position: absolute; left: 86px; }

  /* Testimonials */
  .reviews-title { left: 0; top: 1807px; width: 1200px; text-align: center; color: var(--white); font-size: 29px; }
  .review-card { position: absolute; top: 1884px; width: 282px; height: 208px; border: 2px solid #6a6a6a; border-radius: 6px; }
  .avatar { position: absolute; top: -30px; left: 106px; width: 70px; height: 70px; border-radius: 50%; background: linear-gradient(180deg, #cfc6bd, #7a7570); border: 3px solid var(--white); }
  .review-quote { position: absolute; top: 50px; left: 40px; width: 202px; text-align: center; font-style: italic; font-size: 13.5px; line-height: 22px; color: #b5b5b5; }
  .quote-mark { position: absolute; font-family: "Exo 2", sans-serif; font-size: 40px; color: var(--teal); line-height: 1; }
  .review-author { position: absolute; top: 128px; width: 100%; text-align: center; font-weight: 600; font-size: 14px; color: var(--teal); }
  .review-stars { position: absolute; top: 150px; width: 100%; text-align: center; font-size: 24px; letter-spacing: 2px; color: var(--star); }
  .arrow { position: absolute; top: 1965px; }

  /* Feature */
  .feature-shape { left: 0; top: 2150px; }
  .feature-title { left: 168px; top: 2338px; font-size: 32px; color: var(--ink); }
  .feature-text { left: 168px; top: 2384px; width: 400px; font-size: 15.5px; line-height: 24px; color: var(--graphite); }
  .btn-feature { left: 164px; top: 2507px; width: 172px; height: 55px; }

  /* Booking */
  .book-bg { left: 0; top: 2560px; width: 1200px; height: 533px; background: linear-gradient(180deg, #1f9b98 0%, #2aa9a6 50%, #1a9390 100%); }
  .book-title { left: 0; top: 2812px; width: 1200px; text-align: center; color: var(--white); font-size: 37px; }
  .book-text { left: 260px; top: 2876px; width: 680px; text-align: center; color: var(--white); font-size: 21px; line-height: 30px; }
  .btn-book { left: 518px; top: 2963px; width: 173px; height: 53px; border: 2px solid var(--white); color: var(--white); }

  /* Footer */
  .site-footer { left: 0; top: 3093px; width: 1200px; height: 186px; background: linear-gradient(180deg, #ffffff 50%, #f0f0f0 100%); }
  .footer-nav { left: 0; top: 42px; width: 1200px; display: flex; justify-content: center; gap: 30px; font-family: "Arimo", sans-serif; font-size: 18px; color: var(--ink); }
  .copyright { left: 0; top: 78px; width: 1200px; text-align: center; font-size: 14px; color: var(--muted); }
  .social { left: 528px; top: 114px; display: flex; gap: 6px; }
  .social span { width: 32px; height: 32px; border-radius: 50%; background: var(--teal); }
</style>
</head>
<body>
<div class="page">

  <!-- Hero -->
  <section class="hero">
    <div class="abs hero-photo" role="img" aria-label="Visitors wearing VR headsets riding a roller coaster"></div>
    <div class="abs hero-shade"></div>
    <header class="abs site-header">
      <div class="abs brand">Orbit Voltix VR</div>
      <nav class="abs main-nav"><span>About</span><span>Our Services</span><span>Book Tickets</span><span>Reviews</span><span>Contact</span></nav>
    </header>
    <h1 class="abs heading hero-title">Virtual Reality Theme Park</h1>
    <p class="abs heading hero-sub">Vivamus porttitor purus nisi</p>
    <a class="btn btn-hero">Book Ticket</a>
    <div class="abs slider-dots"><span></span><span class="active"></span><span></span></div>
    <svg class="abs" style="left:0;top:600px" width="1200" height="200" viewBox="0 0 1200 200">
      <defs><linearGradient id="heroBand" x1="0" x2="1"><stop offset="0" stop-color="#b7e0de"/><stop offset=".5" stop-color="#5fb8b5"/><stop offset="1" stop-color="#1f8d8a"/></linearGradient></defs>
      <path d="M0 118 Q600 -10 1200 110 L1200 200 L0 200 Z" fill="url(#heroBand)"/>
      <path d="M0 160 Q520 40 1200 112 L1200 200 L0 200 Z" fill="#ffffff"/>
    </svg>
  </section>

  <!-- About -->
  <section class="about">
    <div class="abs about-photo" role="img" aria-label="Roller coaster cars looping against a city skyline"></div>
    <h2 class="abs heading about-title">About <span style="display:inline;color:var(--ink)">Orbit</span><span>Voltix VR</span></h2>
    <p class="abs about-text">Pellentesque faucibus Ut accumsan ultricies elit Maecenas at justo id velit placerat molestie Donec dictum lectus non odio Cras a ante vitae enim iaculis aliquam Mauris nunc quam venenatis nec euismod sit amet egestas placerat est Pellentesque habitant morbi tristique senectus et n</p>
    <a class="btn btn-outline btn-about">Read More</a>
  </section>

  <!-- Services -->
  <div class="abs dark-photo" role="img" aria-label="Dark roller coaster track structure"></div>
  <section class="services">
    <svg class="abs services-shape" width="1200" height="640" viewBox="0 0 1200 640">
      <defs><linearGradient id="tealBand" x1="0" x2="1"><stop offset="0" stop-color="#145f5d"/><stop offset=".5" stop-color="#1b8482"/><stop offset="1" stop-color="#23a3a0"/></linearGradient></defs>
      <path d="M0 0 H1200 V120 Q620 -40 0 150 Z" fill="#ffffff"/>
      <path d="M0 120 Q260 20 640 40 Q340 40 0 150 Z" fill="#eeeeee"/>
      <path d="M0 150 Q620 -40 1200 120 L1200 480 Q620 700 0 420 Z" fill="url(#tealBand)"/>
      <path d="M1200 480 Q1000 600 820 600 Q1030 610 1200 510 Z" fill="#b9bcbd"/>
    </svg>
    <h2 class="abs heading services-title">Our Services</h2>

    <div class="service-card" style="left:164px;top:1323px">
      <div class="photo" role="img" aria-label="Person wearing a VR headset in free roam play" style="background:linear-gradient(160deg,#6c6c6c,#3b3b3b)"></div>
      <div class="label" style="top:110px">Free Roam VR<br>Experiences</div>
      <svg style="top:178px" width="28" height="34" viewBox="0 0 28 34"><path d="M14 2 V30 M3 20 L14 31 L25 20" stroke="#fff" stroke-width="3" fill="none"/></svg>
    </div>
    <div class="service-card" style="left:387px;top:1373px">
      <div class="photo" role="img" aria-label="Player on a VR treadmill" style="background:linear-gradient(160deg,#8a8a8a,#4a4a4a)"></div>
      <div class="label" style="top:135px">Trundla</div>
      <svg style="top:180px" width="28" height="34" viewBox="0 0 28 34"><path d="M14 2 V30 M3 20 L14 31 L25 20" stroke="#fff" stroke-width="3" fill="none"/></svg>
    </div>
    <div class="service-card" style="left:610px;top:1323px">
      <div class="photo" role="img" aria-label="Person at a stand alone VR station" style="background:linear-gradient(160deg,#6a5040,#3a2f28)"></div>
      <div class="label" style="top:120px">Stand Alone<br>VR Stations</div>
      <svg style="top:178px" width="28" height="34" viewBox="0 0 28 34"><path d="M14 2 V30 M3 20 L14 31 L25 20" stroke="#fff" stroke-width="3" fill="none"/></svg>
    </div>
    <div class="service-card" style="left:832px;top:1373px">
      <div class="photo" role="img" aria-label="Roller coaster loop seen from below" style="background:linear-gradient(160deg,#5b6a78,#22262b)"></div>
      <div class="label" style="top:120px">VR Simulator<br>Rides</div>
      <svg style="top:178px" width="28" height="34" viewBox="0 0 28 34"><path d="M14 2 V30 M3 20 L14 31 L25 20" stroke="#fff" stroke-width="3" fill="none"/></svg>
    </div>
  </section>

  <!-- Testimonials -->
  <section class="reviews">
    <h2 class="abs heading reviews-title">What People Says</h2>
    <svg class="arrow" style="left:120px" width="24" height="40" viewBox="0 0 24 40"><path d="M20 4 L4 20 L20 36" stroke="#9a9a9a" stroke-width="4" fill="none"/></svg>
    <svg class="arrow" style="left:1056px" width="24" height="40" viewBox="0 0 24 40"><path d="M4 4 L20 20 L4 36" stroke="#9a9a9a" stroke-width="4" fill="none"/></svg>

    <div class="review-card" style="left:160px">
      <div class="avatar" role="img" aria-label="Reviewer portrait"></div>
      <span class="quote-mark" style="left:22px;top:34px">“</span>
      <p class="review-quote">Morbi diam mauris viverra in gravido eu mattis in ante Morbi eget arcu Morbi porta libero</p>
      <span class="quote-mark" style="left:240px;top:100px">”</span>
      <div class="review-author">By Author Name</div>
      <div class="review-stars">★★★★★</div>
    </div>
    <div class="review-card" style="left:460px">
      <div class="avatar" role="img" aria-label="Reviewer portrait"></div>
      <span class="quote-mark" style="left:22px;top:34px">“</span>
      <p class="review-quote">Morbi diam mauris viverra in gravido eu mattis in ante Morbi eget arcu Morbi porta</p>
      <span class="quote-mark" style="left:212px;top:100px">”</span>
      <div class="review-author">By Author Name</div>
      <div class="review-stars">★★★★★</div>
    </div>
    <div class="review-card" style="left:760px">
      <div class="avatar" role="img" aria-label="Reviewer portrait"></div>
      <span class="quote-mark" style="left:22px;top:34px">“</span>
      <p class="review-quote">Morbi diam mauris viverra in gravido eu mattis in ante Morbi eget arcu Morbi porta liber</p>
      <span class="quote-mark" style="left:232px;top:100px">”</span>
      <div class="review-author">By Author Name</div>
      <div class="review-stars">★★★★★</div>
    </div>
  </section>

  <!-- Booking backdrop -->
  <div class="abs book-bg" role="img" aria-label="Teal tinted view of a theme park ride"></div>

  <!-- Feature -->
  <section class="feature">
    <svg class="abs feature-shape" width="1200" height="580" viewBox="0 0 1200 580" role="img" aria-label="Young woman in a VR headset leaping beside a roller coaster">
      <defs>
        <linearGradient id="featureFill" x1="0" x2="1" y1="0" y2="0">
          <stop offset="0" stop-color="#e6a04a"/>
          <stop offset=".15" stop-color="#eef2f5"/>
          <stop offset=".55" stop-color="#dfe8ef"/>
          <stop offset=".75" stop-color="#f0d23a"/>
          <stop offset="1" stop-color="#9fb3c6"/>
        </linearGradient>
        <linearGradient id="tealEdge" x1="0" x2="1"><stop offset="0" stop-color="#2aa7a4"/><stop offset="1" stop-color="#1a8a87"/></linearGradient>
      </defs>
      <path d="M0 110 Q420 -10 1200 90 L1200 400 Q700 560 0 520 Z" fill="url(#featureFill)"/>
      <path d="M0 110 Q420 -10 1200 90 L1200 80 Q420 -20 0 100 Z" fill="url(#tealEdge)"/>
    </svg>
    <h2 class="abs heading feature-title">Best Virtual Reality</h2>
    <p class="abs feature-text">Pellentesque faucibus Ut accumsan ultricies elit Maecenas at justo id velit placerat molestie Donec dictum lectus non odio Cras a ante vitae enim iaculis aliquam Mauris nunc quam venenatis nec</p>
    <a class="btn btn-outline btn-feature">Read More</a>
  </section>

  <!-- Booking -->
  <section class="book">
    <h2 class="abs heading book-title">Book Online Now</h2>
    <p class="abs book-text">Pellentesque faucibus Ut accumsan ultricies elit Maecenas at justo id velit placerat molestie Donec dictum lectus non odio Cras a an</p>
    <a class="btn btn-book">Click Here</a>
  </section>

  <!-- Footer -->
  <footer class="abs site-footer">
    <nav class="abs footer-nav"><span>About</span><span>Our Services</span><span>Book Tickets</span><span>Reviews</span><span>Contact</span></nav>
    <p class="abs copyright">© 2019 Company Name  All right reserved</p>
    <div class="abs social"><span></span><span></span><span></span><span></span></div>
  </footer>

</div>
</body>
</html>
```